Site for entrepreneurs/small businesses needs Logo, Homepage

Looking for a logo, either an icon, or stylized text, or a combination of both, and a home page design which fits with it. The logo will be for use on the public website as well as for printed collateral (business cards, post cards, brochures and various other marketing materials).

The site is called Orbitwell (Orbitwell.example). This is to be a national, and eventually an international brand. The new service will provide an easy-to-use platform for entrepreneurs to build their business and web presence together in an integrated way which allows them to focus on their core competency.

The site/service will be dead-simple to use, A/B/C, 1/2/3. We will want some sort of "Get started for FREE" promotional space to collect the person's email address with multiple points of interest which guide the user back to this one call to action: sign up for free. We will feature editorial/blog stories, customer testimonials, and present several key features the the reader just can't live without if they are starting a new business.

Criteria:
* Refer to our comparable sites/logos in the design document attached
* Incorporate our color scheme (but complementary colors welcome)
* No Serif fonts!
* No photo-realistic elements for logo
* Logo must present well in gray scale and/or black/white (for printed materials)
* Strokes/borders that are wider to promote simplicity (vs. thin/precise lines which promote technical complexity)

Inspirations:
* Creative/Custom (but legible) fonts
* Excitement, energetic, jumping for joy
* Karate / Ninja / Power / Precision
* Dance Moves
* Regional influences: California, Silicon Valley, West Coast, Surf City, Beaches, Sunset
* Simple/easy, no-brainer solutions

Target Market(s)

Small Businesses / Entrepreneurs

Logo Text

Orbitwell or Orbitwell.example

Number of Pages Required

1 page

Font styles to use
Sans Serif
Decorative

Requirements
Must have
• See the attached style guide (PDF)

```html
<!DOCTYPE html>
<html lang="en">
<head>
<meta charset="utf-8">
<title>Orbitwell – Home</title>
<link href="https://fonts.googleapis.com/css2?family=Lato:ital,wght@0,400;0,700;0,900;1,400&display=swap" rel="stylesheet">
<style>
:root{
  --orange:#ff8a00;
  --navy:#0f1f4a;
  --navy-deep:#0a1a40;
  --panel:#1d1f45;
  --sky:#6e9fdc;
  --sky-mid:#5a86c8;
  --card:#2a4f86;
  --purple:#5a168f;
  --indigo:#2c3f8c;
  --white:#ffffff;
  --ink:#1c1c1c;
  --footer:#ececec;
  --bubble:#ececec;
}
*{box-sizing:border-box;margin:0;padding:0}
html,body{width:1200px;height:2946px;overflow:hidden}
body{font-family:'Lato',Arial,sans-serif;color:var(--white);position:relative;background:var(--white)}
.section{position:absolute;left:0;width:1200px;overflow:hidden}
.btn{position:absolute;background:var(--orange);color:var(--white);font-weight:700;font-size:17px;border-radius:26px;display:flex;align-items:center;justify-content:center;height:50px}
.art{position:absolute;border-radius:6px}
.lead{position:absolute;font-size:16px;line-height:28px;color:var(--white)}
.kicker{font-weight:700;font-size:46px;line-height:1}
.headline{font-weight:900;font-size:74px;line-height:1}

/* header */
.site-header{top:0;height:90px;background:var(--white)}
.brand{position:absolute;left:76px;top:18px;display:flex;align-items:center;gap:14px;color:var(--ink);font-weight:900;font-size:25px}
.brand-dot{width:56px;height:56px;border-radius:50%;border:5px solid #e0392b}
.nav{position:absolute;right:78px;top:38px;display:flex;gap:54px;font-size:13px;font-weight:700;color:var(--ink)}
.nav .active{color:var(--orange)}

/* hero */
.hero{top:90px;height:502px;background:linear-gradient(90deg,var(--purple) 0%,#3e1f8e 55%,var(--indigo) 100%)}
.hero-art{left:62px;top:70px;width:540px;height:380px;background:linear-gradient(180deg,#e6f4ff 0%,#8dc1ef 100%);opacity:.9}
.hero-copy{position:absolute;left:678px;top:70px}
.hero-copy .kicker{font-size:36px}
.hero-copy .headline{font-size:76px}
.hero-copy p{font-size:15.5px;line-height:26px;width:440px;margin-top:14px}
.signup{position:absolute;left:678px;top:265px;width:448px;height:187px;background:var(--panel);border-radius:10px}
.signup h2{text-align:center;font-weight:900;font-size:32px;margin-top:18px}
.email{position:absolute;left:30px;top:72px;width:388px;height:44px;background:var(--white);border-radius:22px;color:var(--ink);font-size:15px;display:flex;align-items:center;justify-content:center}
.signup .btn{left:30px;top:124px;width:388px;height:44px;font-size:19px}

/* about */
.about{top:592px;height:518px;background:linear-gradient(90deg,#123a7a 0%,#0b2350 100%)}
.about-team{left:590px;top:55px;width:505px;height:430px;background:linear-gradient(180deg,#2c3e5e 0%,#1a2440 100%);opacity:.85}
.about-copy{position:absolute;left:75px;top:135px}
.about .lead{left:75px;top:278px;width:440px}
.about .btn{left:75px;top:420px;width:166px}

/* features */
.features{top:1110px;height:645px;background:var(--sky)}
.feature-card{position:absolute;width:193px;background:var(--card);border-radius:8px;box-shadow:0 6px 12px rgba(0,0,0,.25);text-align:center;padding:22px 18px 0}
.feature-card h3{font-size:20px;font-weight:700;margin-top:12px}
.feature-card p{font-size:13.5px;line-height:21px;margin-top:8px}
.feature-copy{position:absolute;left:630px;top:157px}
.features .lead{left:630px;top:305px;width:460px}
.features .btn{left:630px;top:456px;width:164px}

/* testimonials */
.testimonials{top:1755px;height:518px;background:var(--navy-deep)}
.testi-copy{position:absolute;left:75px;top:70px}
.testimonials .btn{left:960px;top:104px;width:166px}
.quote{position:absolute;top:225px;width:330px;height:170px;background:var(--bubble);border-radius:10px;color:var(--ink);font-style:italic;font-size:14px;line-height:26px;padding:22px 30px}
.quote-tail{position:absolute;left:70px;bottom:-22px}
.avatar{position:absolute;right:28px;bottom:-16px;width:68px;height:68px;border-radius:50%;background:var(--white);display:flex;align-items:center;justify-content:center}
.quote-name{position:absolute;top:458px;font-size:17px;font-weight:700}

/* blog */
.blog{top:2273px;height:532px;background:var(--sky)}
.blog-art{left:60px;top:85px;width:555px;height:380px;background:linear-gradient(180deg,#cfe1f5 0%,#9bbde6 100%);opacity:.85}
.blog-copy{position:absolute;left:678px;top:88px}
.blog .lead{left:678px;top:225px;width:460px}
.blog .btn{left:678px;top:380px;width:162px;height:46px}

/* footer */
.site-footer{top:2805px;height:141px;background:var(--footer);color:var(--ink)}
.foot-nav{position:absolute;left:75px;top:45px;display:flex;gap:52px;font-size:12.5px;font-weight:700}
.copyright{position:absolute;left:75px;top:82px;font-size:12.5px}
.socials{position:absolute;right:78px;top:50px;display:flex;gap:22px}
.socials span{width:30px;height:30px;border-radius:50%;background:var(--ink)}
</style>
</head>
<body>

<header class="section site-header">
  <div class="brand"><span class="brand-dot"></span>Orbitwell</div>
  <nav class="nav">
    <span class="active">HOME</span><span>ABOUT US</span><span>FEATURES</span><span>BLOG</span><span>TESTIMONIALS</span><span>CONTACT US</span>
  </nav>
</header>

<section class="section hero">
  <div class="art hero-art" role="img" aria-label="Illustration of a team working at desks with laptops in front of a growth chart"></div>
  <div class="hero-copy">
    <div class="kicker">Welcome to</div>
    <div class="headline">Orbitwell</div>
    <p>Lorem ipsum dolor sit amet, consectetur adipiscing elit curabitur arcu sem, egestas id leo sed..</p>
  </div>
  <div class="signup">
    <h2>Get Started for FREE</h2>
    <div class="email">Enter Email Address</div>
    <div class="btn">Sign Up for Free</div>
  </div>
</section>

<section class="section about">
  <svg width="1200" height="518" style="position:absolute;left:0;top:0">
    <polygon points="0,0 330,0 870,518 0,518" fill="#5a86c8"/>
  </svg>
  <div class="art about-team" role="img" aria-label="Illustration of a group of business people standing together"></div>
  <div class="about-copy">
    <div class="kicker">About</div>
    <div class="headline">Orbitwell</div>
  </div>
  <p class="lead">Lorem ipsum dolor sit amet, consectetur adipiscing elit. Curabitur arcu sem, egestas id leo sed, pharetra pulvinar urna. Ut non ultrices lectus ut urna quis nibh vestibulum iaculis vel ligula metus..</p>
  <div class="btn">Read More</div>
</section>

<section class="section features">
  <div class="feature-card" style="left:112px;top:86px;height:195px">
    <svg width="56" height="50" viewBox="0 0 56 50"><rect x="4" y="12" width="48" height="36" rx="5" fill="#fff"/><rect x="19" y="3" width="18" height="12" rx="3" fill="none" stroke="#fff" stroke-width="5"/><rect x="15" y="12" width="4" height="36" fill="#2a4f86"/><rect x="37" y="12" width="4" height="36" fill="#2a4f86"/></svg>
    <h3>Vivamus</h3>
    <p>Lorem ipsum dolor sit amet ut urna quis nibh lorem..</p>
  </div>
  <div class="feature-card" style="left:345px;top:86px;height:260px">
    <svg width="70" height="54" viewBox="0 0 70 54"><polyline points="6,4 6,48 66,48" fill="none" stroke="#fff" stroke-width="5"/><polyline points="14,38 28,22 40,32 60,10" fill="none" stroke="#fff" stroke-width="5"/><polygon points="52,8 64,6 62,18" fill="#fff"/></svg>
    <h3>Vivamus</h3>
    <p>Lorem ipsum dolor sit amet ut urna quis nibh lorem posuere ipsum nec arcu..</p>
  </div>
  <div class="feature-card" style="left:112px;top:308px;height:257px">
    <svg width="70" height="56" viewBox="0 0 70 56"><circle cx="35" cy="14" r="10" fill="#fff"/><circle cx="14" cy="20" r="8" fill="#fff"/><circle cx="56" cy="20" r="8" fill="#fff"/><path d="M20 54a15 15 0 0 1 30 0z" fill="#fff"/><path d="M2 50a12 12 0 0 1 22 -6v6z" fill="#fff"/><path d="M68 50a12 12 0 0 0 -22 -6v6z" fill="#fff"/></svg>
    <h3>Vivamus</h3>
    <p>Lorem ipsum dolor sit amet ut urna quis nibh lorem posuere ipsum nec arcu..</p>
  </div>
  <div class="feature-card" style="left:345px;top:373px;height:192px">
    <svg width="70" height="52" viewBox="0 0 70 52"><rect x="12" y="4" width="46" height="34" rx="3" fill="none" stroke="#fff" stroke-width="5"/><rect x="2" y="42" width="66" height="7" rx="3" fill="#fff"/></svg>
    <h3>Vivamus</h3>
    <p>Lorem ipsum dolor sit amet ut urna quis nibh lorem..</p>
  </div>
  <div class="feature-copy">
    <div class="kicker">Orbitwell</div>
    <div class="headline">Key Features</div>
  </div>
  <p class="lead">Lorem ipsum dolor sit amet, consectetur adipiscing elit. Curabitur arcu sem, egestas id leo sed, pharetra pulvinar urna. Ut non ultrices lectus ut urna quis nibh vestibulum iaculis vel ligula metus..</p>
  <div class="btn">Read More</div>
</section>

<section class="section testimonials">
  <svg width="1200" height="518" style="position:absolute;left:0;top:0">
    <polygon points="1200,0 1200,518 285,518" fill="#5a86c8"/>
  </svg>
  <div class="testi-copy">
    <div class="kicker">Customer</div>
    <div class="headline">Testimonials</div>
  </div>
  <div class="btn">Read All</div>

  <div class="quote" style="left:75px">“ Lorem ipsum dolor sit amet, consectetur adipiscing elit. Curabitur arcu sem, egestas id leo sed, pharetra pulvinar urna. Ut non ultrices lectus ut urna quis nibh vestibulum iaculis vel ligula metus..”
    <svg class="quote-tail" width="30" height="24"><polygon points="0,0 28,0 4,24" fill="#ececec"/></svg>
    <div class="avatar"><svg width="28" height="30" viewBox="0 0 28 30"><circle cx="14" cy="8" r="7" fill="#0f1f4a"/><path d="M1 30a13 13 0 0 1 26 0z" fill="#0f1f4a"/></svg></div>
  </div>
  <div class="quote" style="left:435px">“ Lorem ipsum dolor sit amet, consectetur adipiscing elit. Curabitur arcu sem, egestas id leo sed, pharetra pulvinar urna. Ut non ultrices lectus ut urna quis nibh vestibulum iaculis vel ligula metus..”
    <svg class="quote-tail" width="30" height="24"><polygon points="0,0 28,0 4,24" fill="#ececec"/></svg>
    <div class="avatar"><svg width="28" height="30" viewBox="0 0 28 30"><circle cx="14" cy="8" r="7" fill="#0f1f4a"/><path d="M1 30a13 13 0 0 1 26 0z" fill="#0f1f4a"/></svg></div>
  </div>
  <div class="quote" style="left:796px">“ Lorem ipsum dolor sit amet, consectetur adipiscing elit. Curabitur arcu sem, egestas id leo sed, pharetra pulvinar urna. Ut non ultrices lectus ut urna quis nibh vestibulum iaculis vel ligula metus..”
    <svg class="quote-tail" width="30" height="24"><polygon points="0,0 28,0 4,24" fill="#ececec"/></svg>
    <div class="avatar"><svg width="28" height="30" viewBox="0 0 28 30"><circle cx="14" cy="8" r="7" fill="#0f1f4a"/><path d="M1 30a13 13 0 0 1 26 0z" fill="#0f1f4a"/></svg></div>
  </div>
  <div class="quote-name" style="left:75px">Name Heading</div>
  <div class="quote-name" style="left:435px">Name Heading</div>
  <div class="quote-name" style="left:796px">Name Heading</div>
</section>

<section class="section blog">
  <div class="art blog-art" role="img" aria-label="Illustration of a businessman presenting growth charts, strategy and analytics icons"></div>
  <div class="blog-copy">
    <div class="kicker">Blog</div>
    <div class="headline">Stories</div>
  </div>
  <p class="lead">Lorem ipsum dolor sit amet, consectetur adipiscing elit. Curabitur arcu sem, egestas id leo sed, pharetra pulvinar urna. Ut non ultrices lectus ut urna quis nibh vestibulum iaculis vel ligula metus..</p>
  <div class="btn">Read All Stories</div>
</section>

<footer class="section site-footer">
  <nav class="foot-nav">
    <span>HOME</span><span>ABOUT US</span><span>FEATURES</span><span>BLOG</span><span>TESTIMONIALS</span><span>CONTACT US</span>
  </nav>
  <div class="copyright">Copyright © 2018 Company Name. All Right Reserved</div>
  <div class="socials" aria-label="Social links"><span></span><span></span><span></span></div>
</footer>

</body>
</html>
```